Briloran Clear Springs needs a new business card design (we produce and sell pure bottled water)

We need a clean modern design for our new business cards, We have an existing logo which ultimately cannot be changed, however it could be slighty improved and the colours adjusted. We have this existing logo on all of our bottles, vehicles etc.

Our company slogan is "Clear from the first sip on".
Along with our relevant company information
(Address, phone, website email etc) we will only be using names and not putting position titles for flexibilty.

We are looking for a clean, minimalist modern design.

You can view our website (if need of an update also!) to see our business.

Industry/Entity Type

Business

Contact Information for Business Card

Staff Name : XXXXXX XXXXXX
Address : 9/41 Tavenor St
Halden Rise QLD 4172
Staff Mobile Number : 04XX XXX XXX
Office Phone Number : 07 3918 2457
Staff Email Address : XXXX@brilorancleargo.com.au
Website : www.brilorancleargo.com.au

Font styles to use
Sans Serif

Colors
cee9f5
33a6d7
0492cd
0455a3
3276b5
85abd2
cedeed

Requirements
Must have
• The ability to edit and change the staff members details as we will need to edit for each respective staff member (7 in total)

```html
<!DOCTYPE html>
<html lang="en">
<head>
<meta charset="utf-8">
<title>Briloran Clear Springs – Business Card</title>
<link href="https://fonts.googleapis.com/css2?family=Open+Sans:wght@400;600;700;800&display=swap" rel="stylesheet">
<style>
  :root {
    --backdrop: #2b2b2b;
    --card: #121212;
    --card-edge: #1c1c1c;
    --brand-blue: #3276b5;
    --icon-blue: #33a6d7;
    --text-white: #ffffff;
    --text-soft: #cfcfcf;
    --divider: #262626;
  }
  * { margin: 0; padding: 0; box-sizing: border-box; }
  html, body {
    width: 1200px;
    height: 900px;
    overflow: hidden;
    background: var(--backdrop);
    font-family: "Open Sans", sans-serif;
  }
  .stage {
    width: 1200px;
    height: 900px;
    display: flex;
    align-items: center;
    justify-content: center;
    gap: 50px;
  }
  .card {
    width: 525px;
    height: 300px;
    background: var(--card);
    border: 1px solid var(--card-edge);
    border-radius: 18px;
    position: relative;
    overflow: hidden;
  }

  /* Front */
  .card-front { display: flex; }
  .brand-panel {
    width: 250px;
    padding: 0 0 0 34px;
    display: flex;
    flex-direction: column;
    justify-content: center;
  }
  .brand-mark {
    display: flex;
    align-items: center;
    gap: 12px;
  }
  .brand-dot {
    width: 26px;
    height: 26px;
    border-radius: 50%;
    background: var(--brand-blue);
    flex: none;
  }
  .brand-name {
    color: var(--brand-blue);
    font-weight: 800;
    font-size: 25px;
    line-height: 1.05;
    text-transform: uppercase;
  }
  .tagline {
    color: var(--text-white);
    font-size: 15px;
    margin-top: 14px;
    white-space: nowrap;
  }
  .panel-divider {
    width: 1px;
    background: var(--divider);
    margin: 28px 0;
  }
  .contact-panel {
    flex: 1;
    padding: 52px 0 0 26px;
    color: var(--text-soft);
    font-size: 13px;
    line-height: 1.4;
  }
  .staff-name {
    color: var(--text-white);
    font-weight: 700;
    font-size: 17px;
    margin-bottom: 6px;
  }
  .address { margin-bottom: 10px; }
  .contact-list { list-style: none; }
  .contact-list li {
    display: flex;
    align-items: center;
    gap: 10px;
    margin-bottom: 3px;
  }
  .contact-icon { width: 12px; height: 12px; flex: none; }
  .website { margin-top: 10px; }

  /* Back */
  .card-back {
    display: flex;
    align-items: center;
    justify-content: center;
  }
  .card-back .brand-dot { width: 34px; height: 34px; background: var(--text-white); }
  .card-back .brand-name { color: var(--text-white); font-size: 34px; }
</style>
</head>
<body>
<main class="stage">
  <section class="card card-front" aria-label="Business card front">
    <div class="brand-panel">
      <div class="brand-mark">
        <span class="brand-dot"></span>
        <span class="brand-name">Briloran<br>Clear Springs</span>
      </div>
      <p class="tagline">Clear from the first sip on</p>
    </div>
    <div class="panel-divider"></div>
    <div class="contact-panel">
      <p class="staff-name">Marlena Coutts</p>
      <p class="address">9/41 Tavenor St<br>Halden Rise QLD 4172</p>
      <ul class="contact-list">
        <li>
          <svg class="contact-icon" viewBox="0 0 12 12" aria-hidden="true"><rect x="3" y="0.5" width="6" height="11" rx="1.2" fill="none" stroke="var(--icon-blue)" stroke-width="1.2"/><circle cx="6" cy="9.6" r="0.7" fill="var(--icon-blue)"/></svg>
          <span>0400 275 918</span>
        </li>
        <li>
          <svg class="contact-icon" viewBox="0 0 12 12" aria-hidden="true"><path d="M2.5 1 L4.5 1 L5.3 3.6 L4 4.6 Q5 7 7.4 8 L8.4 6.7 L11 7.5 L11 9.5 Q11 11 9.5 11 Q1 10 1 2.5 Q1 1 2.5 1 Z" fill="var(--icon-blue)"/></svg>
          <span>07 3918 2457</span>
        </li>
        <li>
          <svg class="contact-icon" viewBox="0 0 12 12" aria-hidden="true"><rect x="0.5" y="2" width="11" height="8" rx="1" fill="var(--icon-blue)"/><path d="M0.8 2.5 L6 6.5 L11.2 2.5" fill="none" stroke="var(--card)" stroke-width="1"/></svg>
          <span>info@brilorancleargo.com.au</span>
        </li>
      </ul>
      <p class="website">www.brilorancleargo.com.au</p>
    </div>
  </section>

  <section class="card card-back" aria-label="Business card back">
    <div class="brand-mark">
      <span class="brand-dot"></span>
      <span class="brand-name">Briloran<br>Clear Springs</span>
    </div>
  </section>
</main>
</body>
</html>
```